Autora necesita un cover para su nuevo libro acerca de empoderamiento femenino*

Diseño de cover para libro digital sobre empoderamiento femenino.

El título del libro es: "Las 7 Raíces del Alma Serena"
Subtítulo: Vive con calma, fuerza y propósito cada día

Autora: Rosalba Quintero

Target Market(s)

Mujeres

Font styles to use
Sans Serif

Requirements
Must have
• El título del libro es: "Las 7 Raíces del Alma Serena"

Autora: Rosalba Quintero
Should not have
• Sin imágenes

```html
<!DOCTYPE html>
<html lang="es">
<head>
<meta charset="UTF-8">
<title>Las 7 Raíces del Alma Serena — Rosalba Quintero</title>
<link rel="stylesheet" href="https://fonts.googleapis.com/css2?family=Cormorant+SC:wght@700&family=Work+Sans:wght@400&family=Poppins:wght@500&display=swap">
<style>
  :root {
    --page-bg: #e6e6e6;
    --cover-navy: #0a2063;
    --cover-navy-deep: #041a5c;
    --title-white: #f2f2f2;
    --accent-gold: #9a9313;
    --subtitle-grey: #dde1ea;
    --scene-blue: #1b3d8f;
    --scene-cyan: #39d5e6;
    --scene-sky: #5f8fd6;
    --band-black: #070a14;
  }
  * { margin: 0; padding: 0; box-sizing: border-box; }
  html, body {
    width: 1200px;
    height: 800px;
    overflow: hidden;
    background: var(--page-bg);
  }
  .canvas {
    position: relative;
    width: 1200px;
    height: 800px;
  }
  .book-cover {
    position: absolute;
    left: 408px;
    top: 93px;
    width: 397px;
    height: 607px;
    background: linear-gradient(180deg, var(--cover-navy-deep) 0%, var(--cover-navy) 100%);
    overflow: hidden;
  }
  .cover-title {
    position: absolute;
    left: 24px;
    top: 30px;
    font-family: "Cormorant SC", Georgia, serif;
    font-weight: 700;
    font-size: 56px;
    line-height: 51px;
    color: var(--title-white);
    text-transform: uppercase;
    white-space: nowrap;
  }
  .cover-title .title-number {
    color: var(--accent-gold);
    font-size: 72px;
  }
  .cover-subtitle {
    position: absolute;
    left: 29px;
    top: 207px;
    font-family: "Work Sans", Arial, sans-serif;
    font-weight: 400;
    font-size: 20px;
    line-height: 28px;
    color: var(--subtitle-grey);
    letter-spacing: 0.02em;
    text-transform: uppercase;
    white-space: nowrap;
  }
  .cover-scene {
    position: absolute;
    left: 0;
    top: 262px;
    width: 397px;
    height: 302px;
    background:
      radial-gradient(ellipse 40% 18% at 78% 8%, rgba(170, 205, 245, 0.6), transparent 70%),
      linear-gradient(180deg, var(--cover-navy) 0%, var(--scene-blue) 22%, #2a5fb8 45%, var(--scene-sky) 62%, var(--scene-cyan) 82%, #173a85 100%);
  }
  .author-band {
    position: absolute;
    left: 0;
    bottom: 0;
    width: 397px;
    height: 43px;
    background: var(--band-black);
    display: flex;
    align-items: center;
    justify-content: center;
  }
  .author-name {
    font-family: "Poppins", Arial, sans-serif;
    font-weight: 500;
    font-size: 25px;
    color: var(--title-white);
    letter-spacing: 0.18em;
  }
</style>
</head>
<body>
  <main class="canvas">
    <section class="book-cover">
      <h1 class="cover-title">Las <span class="title-number">7</span> Raíces<br>del Alma<br>Serena</h1>
      <p class="cover-subtitle">Vive con calma, fuerza<br>y propósito cada día</p>
      <div class="cover-scene" role="img" aria-label="Ilustración de una ciudad azul con gráfico de barras ascendente y siluetas de cinco mujeres de negocios"></div>
      <footer class="author-band">
        <span class="author-name">Rosalba Quintero</span>
      </footer>
    </section>
  </main>
</body>
</html>
```